Bright Harbor Counseling Letterhead for hip modern business

I would like some ombre use of the colors in the logo hip letterhead that incorporates logo colors and feel, needs to connect with young professionals and college students. i need to be able to write letters to schools to excuse absences as well. i like color blocks on one side preferably using colors from the attached logo design.

Target Market(s)

high income young people, young adults and college students

Industry/Entity Type

mental health

Font styles to use
Serif
Sans Serif

Colors
0054AA
0677BA
7BADD7
CADEEF
E8F1F8
0094D4
00A9DD
6FCCEA
C7EBF8
E9F6FB
00AB8E
00BBA5
67D7C9
C6EFE9
E9F9F6
59FF00
82FF00
B8FF75
E3FFCB
F4FFEA
A7469A
B969AE
D3A5CF
EDDBEB
F8F0F9
6B429C
8869AF
B7A5CE
E3DAEB
F3F0F8

Requirements
Must have
• a modern hip feel, somewhat color

```html
<!DOCTYPE html>
<html lang="en">
<head>
<meta charset="utf-8">
<title>Bright Harbor Counseling Letterhead</title>
<link href="https://fonts.googleapis.com/css2?family=Open+Sans:wght@300;400;700&display=swap" rel="stylesheet">
<style>
  :root {
    --backdrop: #dfe8f2;
    --paper: #ffffff;
    --plum: #a7469a;
    --plum-soft: #eddbeb;
    --violet-soft: #e3daeb;
    --sky-soft: #e9f6fb;
    --blue-soft: #e8f1f8;
    --ink: #3a3a3a;
    --ink-muted: #666;
    --rule: #999;
  }
  html, body {
    margin: 0;
    width: 1200px;
    height: 784px;
    overflow: hidden;
    background: var(--backdrop);
    font-family: "Open Sans", Arial, sans-serif;
  }
  .letterhead {
    position: absolute;
    left: 338px;
    top: 22px;
    width: 524px;
    height: 740px;
    background: linear-gradient(180deg, var(--paper) 60%, #f7f8fd 100%);
    box-shadow: 0 6px 18px rgba(40, 70, 110, 0.18);
    overflow: hidden;
  }
  .top-rule {
    position: absolute;
    left: 0; top: 0;
    width: 100%;
    height: 4px;
    background: var(--plum);
  }
  .brand {
    position: absolute;
    top: 34px;
    right: 62px;
    display: flex;
    align-items: center;
    gap: 12px;
  }
  .brand-name {
    font-weight: 300;
    color: var(--ink);
    line-height: 1;
    text-align: right;
  }
  .brand-name .primary { display: block; font-size: 27px; }
  .brand-name .secondary {
    display: block;
    font-size: 13px;
    letter-spacing: 3px;
    margin-top: 5px;
  }
  .brand-dot {
    width: 34px;
    height: 34px;
    border-radius: 50%;
    background: var(--plum);
    flex: none;
  }
  .side-wash {
    position: absolute;
    right: 0;
    top: 170px;
    width: 150px;
    height: 190px;
    background: linear-gradient(100deg, rgba(233,246,251,0) 0%, var(--sky-soft) 35%, var(--plum-soft) 70%, var(--violet-soft) 100%);
    opacity: .8;
  }
  .soft-cloud {
    position: absolute;
    left: 70px;
    top: 380px;
    width: 290px;
    height: 230px;
    border-radius: 50%;
    background: radial-gradient(ellipse at center, rgba(233,222,240,.75) 0%, rgba(233,246,251,.55) 55%, rgba(255,255,255,0) 75%);
  }
  .contact {
    position: absolute;
    left: 24px;
    bottom: 32px;
    width: 400px;
    text-align: center;
    font-size: 9px;
    line-height: 1.3;
    white-space: nowrap;
  }
  .contact .address { color: var(--plum); font-weight: 700; margin-bottom: 5px; }
  .icon-row {
    display: flex;
    align-items: center;
    justify-content: center;
    gap: 6px;
    margin-bottom: 5px;
  }
  .icon-row .rule { width: 52px; height: 1px; background: var(--rule); }
  .icon-row svg { width: 12px; height: 12px; }
  .contact .details { color: var(--ink-muted); }
</style>
</head>
<body>
  <main class="letterhead">
    <div class="top-rule"></div>

    <header class="brand">
      <div class="brand-name">
        <span class="primary">Bright Harbor</span>
        <span class="secondary">Counseling</span>
      </div>
      <span class="brand-dot"></span>
    </header>

    <div class="side-wash" role="img" aria-label="Soft pastel colour block decoration in sky, lilac and violet tones"></div>

    <div class="soft-cloud" role="img" aria-label="Soft pastel wash decoration in lilac and pale blue"></div>

    <footer class="contact">
      <div class="address">0000 Sample Way, Ste 210, California, 90000, United States</div>
      <div class="icon-row">
        <span class="rule"></span>
        <svg viewBox="0 0 12 12" aria-label="Address"><circle cx="6" cy="6" r="6" fill="#a7469a"/><path d="M6 2.5a2 2 0 0 0-2 2c0 1.6 2 4 2 4s2-2.4 2-4a2 2 0 0 0-2-2z" fill="#fff"/></svg>
        <svg viewBox="0 0 12 12" aria-label="Phone"><circle cx="6" cy="6" r="6" fill="#a7469a"/><path d="M4 3l1.2 1.4-.6.8a4 4 0 0 0 2.2 2.2l.8-.6L9 8 8.3 9C6 9 3 6 3 3.7z" fill="#fff"/></svg>
        <svg viewBox="0 0 12 12" aria-label="Mobile"><circle cx="6" cy="6" r="6" fill="#a7469a"/><rect x="4.2" y="2.5" width="3.6" height="7" rx=".6" fill="#fff"/></svg>
        <svg viewBox="0 0 12 12" aria-label="Email"><circle cx="6" cy="6" r="6" fill="#a7469a"/><rect x="3" y="4" width="6" height="4.2" fill="#fff"/><path d="M3 4l3 2.3L9 4" stroke="#a7469a" stroke-width=".7" fill="none"/></svg>
        <svg viewBox="0 0 12 12" aria-label="Website"><circle cx="6" cy="6" r="6" fill="#a7469a"/><circle cx="6" cy="6" r="3.2" fill="none" stroke="#fff" stroke-width=".8"/><path d="M2.8 6h6.4M6 2.8v6.4" stroke="#fff" stroke-width=".7"/></svg>
        <span class="rule"></span>
      </div>
      <div class="details">(000) 000-0000 | (000) 000-0000 | info@brightharbor.com | www.brightharbor.com</div>
    </footer>
  </main>
</body>
</html>
```